Flyer Design Project for Sports Medicine Services

I am a sports medicine doctor specialising in the diagnosis and management of sport and exercise injuries for all ages and levels of activity - from elite to weekend jogger. I work under the Business name Peak Stride Athletics and do have a company logo. I am wanting a flier that I can send to family doctors, physiotherapists and sports clubs explaining who I am what I can offer and why they should send me patients.
- I have a Masters in Sports Medicine (MSportsMed), Diplomas in Obstetrics/Gynaecology (DRANZCOG) and also Paediatrics (DCH) and certificate in advanced clinical hypnosis
-accurate diagnosis and management plan with their regular physio to return the player / athlete to the field / court /gym as soon as safely possible
-hypnosis for sports performance eg anxiety control, confidence and mental rehearsal for individuals and teams
- because there are many possible therapists and therapy options, as a sports doctor I can work out who they need to see a physiotherapist, surgeon, massage therapist chiropractor or podiatrist to return them to activity or whether cortisone, PRP or autologous blood injections are needed
-can provide one point of contact for coaches and clubs for rehabilitation and return to sport advice.
- work with Laura Pemberton ex Australian Athlete, a Performance Strategist (NLB listed resource person) and registered Psychologist for best mental preparation for individuals teams and coach development
- can organise rapid access to MRI, ultrasound and specialist appointments if needed
-I work at 3 practices KinetaCare 518 Hollis Rd Hollis 84619027 Monday Wednesday Friday; Brackley Sports Clinic, 193 Brackley Rd, Adelaide 81946372 Tuesday Riverton Hawks Sports Medicine Clinic, Tolvane Arena 8162 5907 Thursday.
-facebook site peakstrideathletics
Updates
Hi All, just to clarify.. My name is Simon Drewett and I am the sports doctor. My wife is Laura Pemberton and she is the psychologist. The flier should mainly be advertising my sports medicine services and a byline ( or at least not the first line in the title) about the Performance Strategy and Coach development.
Target Market(s)
family doctors (GPs), Sporting Clubs, Physiotherapists
Industry/Entity Type
Massage
Look and feel

```html
<!DOCTYPE html>
<html lang="en">
<head>
<meta charset="utf-8">
<title>Peak Stride Athletics – Sports Medicine Flyer</title>
<link href="https://fonts.googleapis.com/css2?family=Roboto+Condensed:wght@400;700&family=Open+Sans:wght@400&family=Arimo:wght@400&display=swap" rel="stylesheet">
<style>
  :root {
    --green: #b5d334;
    --green-deep: #9fc12a;
    --blue: #29a8e0;
    --black: #0b0b0b;
    --white: #ffffff;
    --ink: #2b2b2b;
    --foliage-a: #2f6b2a;
    --foliage-b: #7aa546;
    --skin-a: #f4e4da;
    --skin-b: #d9a88c;
  }
  * { box-sizing: border-box; margin: 0; padding: 0; }
  html, body { width: 881px; height: 1200px; overflow: hidden; background: var(--white); }
  .flyer { position: relative; width: 881px; height: 1200px; overflow: hidden; }
  .flyer-shapes { position: absolute; inset: 0; }

  .brand-name {
    position: absolute; left: 40px; top: 140px; width: 260px;
    font-family: "Roboto Condensed", Arial, sans-serif; font-weight: 700;
    font-size: 31px; line-height: 33px; color: var(--blue);
  }

  .headline {
    position: absolute; left: 0; width: 881px; top: 570px;
    text-align: center; color: var(--white);
    font-family: "Roboto Condensed", Arial, sans-serif; font-weight: 400;
  }
  .headline-service { font-size: 41px; line-height: 48px; padding-left: 60px; }
  .headline-byline { font-size: 52px; line-height: 62px; padding-left: 20px; }

  .intro {
    position: absolute; left: 58px; top: 705px; width: 790px;
    font-family: "Open Sans", Arial, sans-serif; font-size: 18.5px; line-height: 27px;
    color: var(--ink); text-align: justify;
  }

  .credentials { position: absolute; left: 58px; top: 812px; width: 792px; list-style: none; }
  .credentials li {
    position: relative; padding-left: 40px; margin-bottom: 18px;
    font-family: "Arimo", Arial, sans-serif; font-size: 17.5px; line-height: 23px;
    color: var(--ink); text-align: justify;
  }
  .tick { position: absolute; left: 0; top: 5px; width: 24px; height: 20px; }

  .locations {
    position: absolute; left: 0; top: 1044px; width: 881px; height: 156px;
    display: flex; padding: 36px 0 0 0;
    font-family: "Arimo", Arial, sans-serif; font-size: 16px; line-height: 21px; color: var(--white);
  }
  .location { padding-left: 40px; }
  .location + .location { border-left: 1.5px solid var(--white); }
  .location-mwf { width: 270px; }
  .location-tue { width: 230px; padding-left: 22px; }
  .location-thu { padding-left: 20px; }
</style>
</head>
<body>
<main class="flyer">
  <svg class="flyer-shapes" width="881" height="1200" viewBox="0 0 881 1200" aria-hidden="false">
    <defs>
      <linearGradient id="foliage" x1="0" y1="0" x2="1" y2="1">
        <stop offset="0" stop-color="var(--foliage-b)"/>
        <stop offset="0.55" stop-color="var(--foliage-a)"/>
        <stop offset="1" stop-color="#5d8a38"/>
      </linearGradient>
      <linearGradient id="skin" x1="0" y1="0" x2="1" y2="0">
        <stop offset="0" stop-color="var(--skin-a)"/>
        <stop offset="1" stop-color="var(--skin-b)"/>
      </linearGradient>
    </defs>

    <rect class="panel-green" x="0" y="440" width="881" height="606" fill="var(--green)"/>

    <rect class="photo-doctor" x="293" y="0" width="588" height="490" fill="url(#foliage)"
          role="img" aria-label="Portrait photo of Dr Simon Drewett smiling in front of garden foliage"/>
    <rect class="photo-treatment" x="0" y="225" width="293" height="265" fill="url(#skin)"
          role="img" aria-label="Photo of hands massaging an athlete's leg"/>

    <path class="corner-black" d="M0 0 H350 C350 150 290 228 150 232 L0 234 Z"
          fill="var(--black)" stroke="var(--white)" stroke-width="9"/>

    <path class="swoosh-blue" d="M0 545 C30 532 60 522 95 512 C60 540 25 575 0 610 Z" fill="var(--blue)"/>
    <path class="swoosh-white" d="M0 488 H881 V548 C640 462 250 468 95 512 C60 524 30 535 0 548 Z" fill="var(--white)"/>
    <path class="swoosh-white-lower" d="M95 512 C300 470 640 470 881 548 V560 C640 485 300 478 70 560 Z" fill="var(--white)"/>

    <rect class="divider-line" x="0" y="1034" width="881" height="10" fill="var(--white)"/>
    <rect class="band-blue" x="0" y="1044" width="881" height="156" fill="var(--blue)"/>
  </svg>

  <div class="brand-name">Peak Stride<br>Athletics</div>

  <header class="headline">
    <h1 class="headline-service">Sport Injuries Diagnosis and Treatment</h1>
    <h2 class="headline-byline">High performance psychology</h2>
  </header>

  <p class="intro">Simon Drewett a Sports Medicine and Exercise Injuries Doctor specialising in the diagnosis and management of sport and exercise injuries for all ages and levels of activity - from elite to weekend jogger.</p>

  <ul class="credentials">
    <li>
      <svg class="tick" viewBox="0 0 24 20"><rect x="1" y="5" width="14" height="14" fill="none" stroke="var(--ink)" stroke-width="2"/><path d="M4 11 L8 16 L22 1" fill="none" stroke="var(--ink)" stroke-width="3"/></svg>
      Simon has a Masters in Sports Medicine (MSportsMed), Diplomas in Obstetrics /Gynaecology (DRANZCOG) and also Paediatrics (DCH) and certificate in advanced clinical hypnosis
    </li>
    <li>
      <svg class="tick" viewBox="0 0 24 20"><rect x="1" y="5" width="14" height="14" fill="none" stroke="var(--ink)" stroke-width="2"/><path d="M4 11 L8 16 L22 1" fill="none" stroke="var(--ink)" stroke-width="3"/></svg>
      Accurate diagnosis and management plan with their regular physio to return the player / athlete to the field / court /gym as soon as safely possible
    </li>
    <li>
      <svg class="tick" viewBox="0 0 24 20"><rect x="1" y="5" width="14" height="14" fill="none" stroke="var(--ink)" stroke-width="2"/><path d="M4 11 L8 16 L22 1" fill="none" stroke="var(--ink)" stroke-width="3"/></svg>
      Hypnosis for sports performance eg anxiety control, confidence and mental rehearsal for individuals and teams
    </li>
    <li>
      <svg class="tick" viewBox="0 0 24 20"><rect x="1" y="5" width="14" height="14" fill="none" stroke="var(--ink)" stroke-width="2"/><path d="M4 11 L8 16 L22 1" fill="none" stroke="var(--ink)" stroke-width="3"/></svg>
      Rapid access to specialists if needed. Rapid referrals for MRI ultrasound and xrays
    </li>
  </ul>

  <footer class="locations">
    <div class="location location-mwf">Monday Wednesday Friday<br>KinetaCare<br>518 Hollis Rd Hollis<br>84619027</div>
    <div class="location location-tue">Tuesday<br>Brackley Sports Clinic<br>193 Brackley Rd, Adelaide<br>81946372</div>
    <div class="location location-thu">Thursday<br>Riverton Hawks Sports Medicine Clinic<br>Tolvane Arena<br>8162 5907</div>
  </footer>
</main>
</body>
</html>
```